New Business Card Design Project

Use the flyer uploaded and website www.brightoakbuilders.com for inspiration.
List Our Services on Backside of business cards
Marcus Delling
Harborline Builders Inc.
Licensed General Contractors
858-471-6093

Contact Information for Business Card

Use the flyer uploaded and website www.brightoakbuilders.com for inspiration. List Our Services on Backside of business cards Marcus Delling Harborline Builders Inc. Licensed General Contractors 858-471-6093

```html
<!DOCTYPE html>
<html lang="en">
<head>
<meta charset="utf-8">
<title>Harborline Builders – Business Card</title>
<link href="https://fonts.googleapis.com/css2?family=Cormorant+Garamond:wght@500&family=Arimo:wght@400&display=swap" rel="stylesheet">
<style>
  :root {
    --backdrop: #dcdcdc;
    --card-dark: #2f2f2f;
    --card-light: #f6f6f6;
    --band-light: #ebebeb;
    --band-grey: #aaa8a9;
    --ink: #2c2c2c;
    --ink-soft: #3a3a3a;
    --white: #ffffff;
  }
  * { margin: 0; padding: 0; box-sizing: border-box; }
  html, body { width: 1200px; height: 1040px; overflow: hidden; }
  body { background: var(--backdrop); position: relative; font-family: "Arimo", Arial, sans-serif; }

  .card {
    position: absolute; left: 286px; width: 644px; height: 366px;
    border-radius: 18px; overflow: hidden;
    box-shadow: 0 2px 4px rgba(0,0,0,.25);
  }
  .card-front { top: 130px; background: var(--card-dark); color: var(--white); }
  .card-back { top: 568px; background: var(--card-light); color: var(--ink); }

  .brand-name {
    position: absolute; left: 0; width: 325px; top: 168px; text-align: center;
    font-family: "Cormorant Garamond", Georgia, serif; font-weight: 500;
    font-size: 24px; letter-spacing: 1.5px; color: var(--white);
  }
  .divider { position: absolute; left: 325px; top: 128px; width: 1px; height: 114px; background: var(--white); }
  .person-name {
    position: absolute; left: 343px; top: 122px;
    font-family: "Cormorant Garamond", Georgia, serif; font-weight: 500;
    font-size: 27px; letter-spacing: 1px;
  }
  .contact-list { position: absolute; left: 345px; top: 175px; list-style: none; font-size: 15.5px; }
  .contact-list li { display: flex; align-items: center; height: 20.5px; }
  .contact-list svg { width: 13px; height: 13px; margin-right: 9px; fill: var(--white); }

  .footer-band { position: absolute; left: 0; bottom: 0; width: 100%; height: 26px; }
  .footer-band svg { position: absolute; inset: 0; }
  .footer-text { position: absolute; top: 5px; font-size: 15.5px; color: var(--ink-soft); }
  .footer-company { left: 52px; }
  .footer-license { left: 362px; }

  .back-brand {
    position: absolute; left: 0; width: 100%; top: 88px; text-align: center;
    font-family: "Cormorant Garamond", Georgia, serif; font-weight: 500;
    font-size: 42px; letter-spacing: 2px; color: var(--ink);
  }
  .services-title {
    position: absolute; left: 0; width: 100%; top: 216px; text-align: center;
    font-family: "Cormorant Garamond", Georgia, serif; font-weight: 500;
    font-size: 21px; letter-spacing: 3px;
  }
  .services-list { position: absolute; left: 0; width: 100%; top: 252px; list-style: none; text-align: center; font-size: 16.5px; color: var(--ink-soft); }
  .services-list li { height: 23.6px; }
  .sep { display: inline-block; width: 7px; height: 7px; background: var(--ink); margin: 0 10px 2px; vertical-align: middle; }
</style>
</head>
<body>
  <section class="card card-front">
    <div class="brand-name">HARBORLINE BUILDERS</div>
    <div class="divider"></div>
    <h1 class="person-name">MARCUS DELLING</h1>
    <ul class="contact-list">
      <li><svg viewBox="0 0 24 24"><path d="M6.6 10.8a15 15 0 0 0 6.6 6.6l2.2-2.2a1 1 0 0 1 1-.25 11.4 11.4 0 0 0 3.6.57 1 1 0 0 1 1 1V20a1 1 0 0 1-1 1A17 17 0 0 1 3 4a1 1 0 0 1 1-1h3.5a1 1 0 0 1 1 1c0 1.25.2 2.45.57 3.6a1 1 0 0 1-.25 1z"/></svg>858-471-6093</li>
      <li><svg viewBox="0 0 24 24"><path d="M2 5h20v14H2z M3.5 6.5 12 13l8.5-6.5" fill="none" stroke="#fff" stroke-width="2"/></svg>info@brightoakbuilders.com</li>
      <li><svg viewBox="0 0 24 24"><circle cx="12" cy="12" r="10"/></svg>www.brightoakbuilders.com</li>
    </ul>
    <div class="footer-band">
      <svg width="644" height="26" viewBox="0 0 644 26">
        <polygon points="0,0 313,0 306,26 0,26" fill="var(--band-light)"/>
        <polygon points="315,0 644,0 644,26 308,26" fill="var(--band-grey)"/>
      </svg>
      <span class="footer-text footer-company">Harborline Builders Inc.</span>
      <span class="footer-text footer-license">Licensed General Contractors</span>
    </div>
  </section>

  <section class="card card-back">
    <div class="back-brand">HARBORLINE BUILDERS</div>
    <h2 class="services-title">SERVICES</h2>
    <ul class="services-list">
      <li>Remodel : Kitchen &amp; Bath<span class="sep"></span>Painting : Interior &amp; Exterior</li>
      <li>Flooring : Carpet, Vinyl, Wood<span class="sep"></span>Window &amp; Door Replacement</li>
      <li>Plumbing : Repairs &amp; Upgrades<span class="sep"></span>Energy- Efficient Upgrades</li>
      <li>Deck &amp; Pation Construction<span class="sep"></span>Water &amp; Mold Damage<span class="sep"></span>Garage Renovation</li>
    </ul>
  </section>
</body>
</html>
```